Design and Renovation Company Luxury Business Card

I want to create a luxury business card for a Design and Renovation Firm . We will use our current logo. The company name is 528BUILDA. We do not want anything standard. We need a very unique concept.
Please see uploaded inspiration. I really like the textured paper option. I would like the card to be thick with debossing, and/or embossing options. The logo has orange in it but I would like to see the card with and without the orange. I think the orange may make the company feel less high-end. The goal is to elevate the logo not match its vibe per se of the logo. We want something very unique, not standard at all!
I would like a space for :
Logo,
Name,
Position,
Email,
Office number,
Website Address,
Business Address,
Thank you!
Have fun!
Target Market(s)
Home owners Age 35 +
Industry/Entity Type
Design and Renovation
Contact Information for Business Card
Logo, Name, Position, Email, Office number, Website Address, Business Address,.
Colors
Designer to choose colors to be used in the design.
Requirements
Must have
- A luxury designer feel. Must be black or dark grey but open to other luxury ideas.
Nice to have
- Gold, silver, black embossing or debossing. Textured paper design.
Should not have
- A cheap look and feel.

```html
<!DOCTYPE html>
<html lang="en">
<head>
<meta charset="utf-8">
<title>528BUILDA Business Card</title>
<link rel="stylesheet" href="https://fonts.googleapis.com/css2?family=Poppins:wght@400;500;600&display=swap">
<style>
  :root {
    --backdrop: #e0e5e6;
    --card: #232326;
    --ink-deep: #0e0e10;
    --orange: #f7941d;
    --white: #ffffff;
    --panel-top: #353535;
    --panel-bottom: #111112;
  }
  * { margin: 0; padding: 0; box-sizing: border-box; }
  html, body {
    width: 1200px;
    height: 960px;
    overflow: hidden;
    background: var(--backdrop);
    font-family: "Poppins", sans-serif;
  }
  .card {
    position: absolute;
    left: 252px;
    width: 700px;
    height: 400px;
    background: var(--card);
    border-radius: 30px;
    border-left: 4px solid var(--orange);
    border-bottom: 4px solid var(--orange);
    overflow: hidden;
  }
  .card--front { top: 60px; }
  .card--back { top: 500px; }

  /* Front */
  .front-brand {
    position: absolute;
    left: 0;
    right: 0;
    top: 168px;
    display: flex;
    justify-content: center;
    align-items: center;
    gap: 18px;
  }
  .front-brand__square {
    width: 34px;
    height: 34px;
    background: var(--orange);
  }
  .front-brand__name {
    font-weight: 600;
    font-size: 48px;
    line-height: 1;
    letter-spacing: 2px;
    color: var(--ink-deep);
  }

  /* Back */
  .brand {
    position: absolute;
    left: 21px;
    top: 22px;
  }
  .brand__square {
    position: absolute;
    left: 0;
    top: 10px;
    width: 30px;
    height: 30px;
    background: var(--orange);
  }
  .brand__name {
    position: absolute;
    left: 44px;
    top: -8px;
    font-weight: 500;
    font-size: 54px;
    line-height: 1;
    letter-spacing: 3px;
    color: var(--white);
    white-space: nowrap;
  }
  .brand__tagline {
    position: absolute;
    left: 50px;
    top: 54px;
    font-weight: 500;
    font-size: 12.5px;
    letter-spacing: 3.6px;
    color: var(--white);
    white-space: nowrap;
  }
  .decor-panel {
    position: absolute;
    right: 0;
    top: 0;
    width: 178px;
    height: 100%;
    background: linear-gradient(200deg, var(--panel-top), var(--panel-bottom) 60%);
  }
  .holder {
    position: absolute;
    left: 0;
    top: 165px;
  }
  .holder__bar {
    position: absolute;
    left: 0;
    top: 2px;
    width: 15px;
    height: 47px;
    background: var(--orange);
  }
  .holder__name {
    position: absolute;
    left: 21px;
    top: -6px;
    font-size: 36px;
    line-height: 1.2;
    color: var(--white);
    white-space: nowrap;
  }
  .holder__first { color: var(--orange); font-weight: 600; }
  .holder__last { font-weight: 400; }
  .holder__role {
    position: absolute;
    left: 22px;
    top: 38px;
    font-weight: 500;
    font-size: 17px;
    color: var(--white);
    white-space: nowrap;
  }
  .address {
    position: absolute;
    left: 22px;
    top: 230px;
    font-style: normal;
    font-size: 18px;
    line-height: 25px;
    color: var(--orange);
    white-space: nowrap;
  }
  .contacts {
    position: absolute;
    left: 22px;
    top: 300px;
    list-style: none;
  }
  .contacts li {
    display: flex;
    align-items: center;
    height: 24.5px;
    font-size: 18.5px;
    color: var(--white);
    white-space: nowrap;
  }
  .contacts svg {
    width: 17px;
    height: 17px;
    margin-right: 13px;
    fill: var(--orange);
    flex-shrink: 0;
  }
</style>
</head>
<body>

<section class="card card--front" aria-label="Card front">
  <div class="front-brand">
    <div class="front-brand__square"></div>
    <div class="front-brand__name">528BUILDA</div>
  </div>
</section>

<section class="card card--back" aria-label="Card back">
  <div class="decor-panel" role="img" aria-label="Dark embossed decorative block"></div>

  <div class="brand">
    <div class="brand__square"></div>
    <div class="brand__name">528BUILDA</div>
    <div class="brand__tagline">Design and Renovation Firm</div>
  </div>

  <div class="holder">
    <div class="holder__bar"></div>
    <div class="holder__name"><span class="holder__first">Marta</span> <span class="holder__last">Velkova</span></div>
    <div class="holder__role">Founder &amp; CEO</div>
  </div>

  <address class="address">
    4120 Maple Crest Dr. Suite 110<br>
    Oak Ridge, TX 75302
  </address>

  <ul class="contacts">
    <li>
      <svg viewBox="0 0 24 24" aria-hidden="true"><path d="M6.6 10.8a15.1 15.1 0 0 0 6.6 6.6l2.2-2.2a1 1 0 0 1 1-.25 11.4 11.4 0 0 0 3.6.57 1 1 0 0 1 1 1V20a1 1 0 0 1-1 1A17 17 0 0 1 3 4a1 1 0 0 1 1-1h3.5a1 1 0 0 1 1 1c0 1.25.2 2.45.57 3.57a1 1 0 0 1-.25 1z"/></svg>
      (555) 214-3067
    </li>
    <li>
      <svg viewBox="0 0 24 24" aria-hidden="true"><path d="M12 2a10 10 0 1 0 0 20 10 10 0 0 0 0-20zm-1 17.9A8 8 0 0 1 4.1 10L9 15v1a2 2 0 0 0 2 2zm6.9-2.5A2 2 0 0 0 16 16h-1v-3a1 1 0 0 0-1-1H8v-2h2a1 1 0 0 0 1-1V7h2a2 2 0 0 0 2-2v-.4a8 8 0 0 1 2.9 12.8z"/></svg>
      info@yourwebsite.com
    </li>
    <li>
      <svg viewBox="0 0 24 24" aria-hidden="true"><path d="M2 8l10-6 10 6v12a1 1 0 0 1-1 1H3a1 1 0 0 1-1-1zm2 1.2V19h16V9.2l-8 5z"/></svg>
      www.yourwebsite.com
    </li>
  </ul>
</section>

</body>
</html>
```